House flipping business web site needed

pinecrestholdingsgroup.example.
I am a residential developer in Northern NJ and I am looking for a fresh new updated website. I have an intro video about my company being made now. I don't update it very often but I want an easy format that I can add update photos to on projects I have worked on or homes I renovate for sale.

Target Market(s)

investors into my projects so a portfolio , people looking to sell their homes to me.

Industry/Entity Type

Real Estate Development

Number of Pages Required

4 page

Font styles to use
Serif

Colors
33b8a4
39a9d7
cadf82

Requirements
Must have
• space for an intro video about my company
• a portfolio with pictures and information about each project
• Markets we serve- Morris County, NJ
• My logo- already created
• SEO
• Yes I would like this to function over all platforms. Phone, computer, all platforms.
• history and background page
• I am looking for a completed page that I can upload to the site that hosts my website
Nice to have
• I want something creative, easy to navigate. modern.

```html
<!DOCTYPE html>
<html lang="en">
<head>
<meta charset="utf-8">
<title>Pinecrest Holdings Group – Home Renovation &amp; Investment in Morris County, NJ</title>
<link href="https://fonts.googleapis.com/css2?family=Roboto:ital,wght@0,400;0,500;0,700;1,400&family=Roboto+Slab:wght@400;500;700&family=Sacramento&display=swap" rel="stylesheet">
<style>
:root{
  --blue:#39a9d7;
  --blue-light:#84d3f8;
  --teal:#33b8a4;
  --green:#cadf82;
  --ink:#222;
  --muted:#555;
  --grey-text:#777;
  --white:#fff;
  --soft:#f3f5f7;
  --line:#7ccabd;
}
*{box-sizing:border-box;margin:0;padding:0}
html,body{width:1200px;height:2446px;overflow:hidden}
body{font-family:"Roboto",Arial,sans-serif;color:var(--ink);background:var(--white);position:relative}
h1,h2,h3,h4,.logo-name,.nav{font-family:"Roboto Slab",Georgia,serif}
.abs{position:absolute}

/* header */
.topbar{position:absolute;left:0;top:0;width:1200px;height:36px;border-top:3px solid #7a8a96;font-size:14px;color:var(--grey-text)}
.topbar .item{position:absolute;top:9px;display:flex;align-items:center;gap:6px;white-space:nowrap}
.sell-pill{position:absolute;left:967px;top:8px;width:109px;height:22px;border-radius:6px;background:var(--teal);color:#fff;font-size:13px;font-weight:500;text-align:center;line-height:22px}
.social-dot{position:absolute;top:13px;width:11px;height:11px;border-radius:50%;background:#9aa5ad}
.logo-box{position:absolute;left:54px;top:30px;width:283px;height:84px;background:#fff;border-radius:0 0 12px 12px;box-shadow:0 2px 6px rgba(0,0,0,.12);display:flex;align-items:center;gap:10px;padding-left:16px}
.logo-mark{flex:none;width:30px;height:30px;border-radius:50%;background:var(--teal)}
.logo-name{font-size:17px;font-weight:500;color:var(--blue);white-space:nowrap}
.nav{position:absolute;top:59px;left:657px;width:495px;height:22px;font-size:15px;font-weight:500;color:var(--ink)}
.nav a{position:absolute;white-space:nowrap;text-decoration:none;color:inherit}

/* hero */
.hero{position:absolute;left:0;top:104px;width:1200px;height:488px;background:linear-gradient(90deg,#6b5a48 0%,#8a8074 35%,#b9b6ae 60%,#a9a59d 100%)}
.hero-line{position:absolute;font-family:"Sacramento",cursive;color:#fff;font-size:50px;white-space:nowrap;line-height:1}
.hero-btn{position:absolute;top:290px;height:32px;background:var(--blue);color:#fff;font-size:11px;font-weight:700;text-align:center;line-height:32px;border-radius:2px}
.dots{position:absolute;left:568px;top:455px;display:flex;gap:8px}
.dots span{width:10px;height:10px;border-radius:50%;background:#fff}
.dots span:first-child{background:transparent;border:1.5px solid #fff}

/* welcome */
.welcome{position:absolute;left:0;top:592px;width:1200px;height:197px;background:linear-gradient(90deg,var(--blue),var(--blue-light));color:#fff;text-align:center}
.welcome h1{font-size:21px;font-weight:700;margin-top:14px}
.dotted-white{position:absolute;left:39px;top:51px;width:1122px;border-top:1.5px dotted rgba(255,255,255,.9)}
.welcome p{font-size:13px;line-height:20px;width:1120px;margin:0 auto}
.welcome .p1{margin-top:25px}
.welcome .p2{margin-top:19px}

/* services */
.section-title{position:absolute;width:1200px;text-align:center;font-size:21px;font-weight:500}
.section-title em{font-style:normal;color:var(--teal)}
.dotted-blue{position:absolute;left:52px;width:1096px;border-top:1.5px dotted var(--line)}
.card{position:absolute;top:911px;width:253px;text-align:center}
.card .photo{width:253px;height:206px;border-bottom:4px solid var(--green)}
.card h3{font-size:17px;font-weight:500;margin-top:22px}
.card p{font-size:12.5px;line-height:20px;color:var(--muted);margin-top:14px}

/* mail + video */
.mail{position:absolute;left:0;top:1239px;width:600px;height:329px;background:linear-gradient(90deg,var(--blue),var(--blue-light))}
.mail h2{position:absolute;top:32px;width:600px;text-align:center;color:#fff;font-size:25px;font-weight:500}
.field{position:absolute;background:#fff;border:1px solid #dde3e8;border-radius:4px;color:#9aa3a9;font-size:12px;text-align:center}
.send{position:absolute;left:225px;top:264px;width:135px;height:34px;background:#fff;border-radius:4px;color:var(--teal);font-size:13px;font-weight:700;text-align:center;line-height:34px}
.video{position:absolute;left:600px;top:1239px;width:600px;height:329px;background:linear-gradient(180deg,#6f9fd4 0%,#a9c9e8 35%,#4a6a48 52%,#3d5260 70%,#2e3c46 100%)}
.play{position:absolute;left:234px;top:101px}

/* testimonials */
.quote{position:absolute;font-size:12.5px;font-style:italic;line-height:20px;color:var(--muted);width:410px}
.quote.left{left:70px;text-align:right}
.quote.right{left:720px;text-align:left}
.who{display:block;font-style:normal;color:var(--ink);margin-top:8px}
.avatar{position:absolute;width:77px;height:77px;border-radius:50%;background:#c8c4bf}
.vline{position:absolute;left:600px;top:1687px;height:220px;border-left:1.5px dotted var(--line)}
.hline{position:absolute;top:1795px;left:52px;width:1096px;border-top:1.5px dotted var(--line)}

/* like bar */
.likebar{position:absolute;left:0;top:1956px;width:1200px;height:72px;background:var(--soft)}
.likebar .rule{position:absolute;top:36px;height:1px;background:#dfe4e8}
.like-pill{position:absolute;left:376px;top:13px;width:447px;height:46px;background:#fff;border-radius:23px;border:1px solid #e3e7ea}
.like-badge{position:absolute;left:121px;top:15px;width:46px;height:16px;background:var(--blue);border-radius:2px}
.like-text{position:absolute;left:173px;top:15px;font-size:11px;color:#444}

/* footer */
.footer{position:absolute;left:0;top:2028px;width:1200px;height:418px;background:linear-gradient(90deg,var(--blue),var(--blue-light));color:#fff}
.footer h4{position:absolute;top:63px;font-size:17px;font-weight:500}
.footer .col{position:absolute;font-size:12.5px;line-height:19.5px}
.map{position:absolute;left:333px;top:93px;width:534px;height:212px;background:linear-gradient(135deg,#cfe0ea,#e9ecef 60%,#d7e6c9)}
.f-social{position:absolute;left:52px;top:275px;display:flex;gap:14px}
.f-social span{width:13px;height:13px;border-radius:50%;background:#fff}
.f-rule{position:absolute;left:52px;top:358px;width:1096px;border-top:1px solid rgba(255,255,255,.7)}
.copy{position:absolute;top:387px;width:1200px;text-align:center;font-size:12.5px;font-weight:500}
</style>
</head>
<body>

<header>
  <div class="topbar">
    <div class="item" style="left:631px">
      <svg width="13" height="13" viewBox="0 0 24 24"><path fill="#888" d="M6.6 10.8a15 15 0 0 0 6.6 6.6l2.2-2.2a1 1 0 0 1 1-.25 11.4 11.4 0 0 0 3.6.57 1 1 0 0 1 1 1V20a1 1 0 0 1-1 1A17 17 0 0 1 3 4a1 1 0 0 1 1-1h3.5a1 1 0 0 1 1 1c0 1.25.2 2.45.57 3.57a1 1 0 0 1-.25 1z"/></svg>
      +1 800 555 01 42
    </div>
    <div class="item" style="left:782px">
      <svg width="14" height="11" viewBox="0 0 24 18"><rect width="24" height="18" rx="2" fill="#888"/><path d="M1 2l11 8 11-8" stroke="#fff" stroke-width="2" fill="none"/></svg>
      info@yourdomain.com
    </div>
    <div class="sell-pill">Sell Your Home</div>
    <span class="social-dot" style="left:1099px"></span>
    <span class="social-dot" style="left:1134px"></span>
  </div>
  <div class="logo-box">
    <span class="logo-mark"></span>
    <span class="logo-name">Pinecrest Holdings Group</span>
  </div>
  <nav class="nav">
    <a style="left:0;color:var(--blue)">HOME</a>
    <a style="left:80px">ABOUT US</a>
    <a style="left:190px">PORTFOLIO</a>
    <a style="left:312px">BLOG</a>
    <a style="left:385px">CONTACT US</a>
  </nav>
</header>

<section class="hero" role="img" aria-label="Photo of a renovated two-storey house with stone wall on a misty wooded lot">
  <div class="hero-line" style="top:160px;left:635px">Investing in our neighborhoods</div>
  <div class="hero-line" style="top:222px;left:690px">Pinecrest Holdings Group</div>
  <div class="hero-btn" style="left:805px;width:79px">CALL NOW</div>
  <div class="hero-btn" style="left:940px;width:105px">GO ON SURFING</div>
  <div class="dots"><span></span><span></span><span></span><span></span></div>
</section>

<section class="welcome">
  <h1>Welcome We’re Pinecrest Holdings Group</h1>
  <div class="dotted-white"></div>
  <p class="p1">Pinecrest Holdings Group is a family run business with 3rd generation builders and renovators in the Morris County area. As the President and owner of Pinecrest Holdings Group I am dedicated to working hard to create opportunities for investment through real estate.</p>
  <p class="p2">At Pinecrest Holdings Group we have a valuable support system and a team of investors, realtors, attorneys, contractors and property managers providing a combined package offering years of experience in the local market.</p>
</section>

<section class="services">
  <h2 class="section-title" style="top:814px">Renovate homes in <em>Morris County</em></h2>
  <div class="dotted-blue" style="top:855px"></div>
  <article class="card" style="left:52px">
    <div class="photo" role="img" aria-label="House under construction with sheathing walls" style="background:linear-gradient(180deg,#b9c3cc,#8a6a4c 55%,#6e5a44)"></div>
    <h3>New Construction</h3>
    <p>Ground-up builds framed and finished by our own crews, start to end.</p>
  </article>
  <article class="card" style="left:333px">
    <div class="photo" role="img" aria-label="Renovated house on a rocky hillside" style="background:linear-gradient(180deg,#d6d8d9,#a49a8a 55%,#6f6a5c)"></div>
    <h3>Full Renovations</h3>
    <p>Dated homes rebuilt inside and out with quality work and fresh design.</p>
  </article>
  <article class="card" style="left:615px">
    <div class="photo" role="img" aria-label="Finished grey colonial house with green lawn" style="background:linear-gradient(180deg,#7fa05c,#9ea6a8 45%,#6f8a4a)"></div>
    <h3>Homes for Sale</h3>
    <p>Move-in ready houses across Morris County, listed once work is done.</p>
  </article>
  <article class="card" style="left:895px">
    <div class="photo" role="img" aria-label="Building shell with wrapped walls on a job site" style="background:linear-gradient(180deg,#6fa6e0,#b8c4cc 50%,#6e6048)"></div>
    <h3>Investor Projects</h3>
    <p>Partner with us on local flips and share in each finished project.</p>
  </article>
</section>

<section class="mail">
  <h2>Feel Free to Mail</h2>
  <div class="field" style="left:49px;top:86px;width:241px;height:33px;line-height:31px">Name *</div>
  <div class="field" style="left:310px;top:86px;width:241px;height:33px;line-height:31px">Email *</div>
  <div class="field" style="left:49px;top:138px;width:502px;height:33px;line-height:31px">Subject</div>
  <div class="field" style="left:49px;top:191px;width:502px;height:55px;padding-top:10px">Write Your Message Here...</div>
  <div class="send">SEND MESSAGE</div>
</section>
<section class="video" role="img" aria-label="Intro video still: lake with wooded shoreline under a cloudy blue sky">
  <svg class="play" width="132" height="132" viewBox="0 0 132 132"><circle cx="66" cy="66" r="60" fill="none" stroke="#fff" stroke-width="9"/><path d="M52 40v52l42-26z" fill="#fff"/></svg>
</section>

<section class="testimonials">
  <h2 class="section-title" style="top:1588px">What <em>People Say</em></h2>
  <div class="dotted-blue" style="top:1628px"></div>
  <div class="vline"></div>
  <div class="hline"></div>

  <p class="quote left" style="top:1683px">Investing alongside the team was simple. Every project came with clear budgets, regular photo updates and a timeline they kept to the week.<span class="who">Evan Morrow , Developer</span></p>
  <div class="avatar" role="img" aria-label="Portrait of Evan Morrow" style="left:490px;top:1687px"></div>
  <div class="avatar" role="img" aria-label="Portrait of Clara Brandt" style="left:632px;top:1687px"></div>
  <p class="quote right" style="top:1683px">We needed to sell our house fast. They made a fair offer, handled the paperwork and closed on the date that suited our family best.<span class="who">Clara Brandt , Manager</span></p>

  <p class="quote left" style="top:1820px">The finished homes speak for themselves. Thoughtful layouts, solid craftsmanship and details buyers notice from the moment they walk in.<span class="who">Nora Haskins , Creative Designer</span></p>
  <div class="avatar" role="img" aria-label="Portrait of Nora Haskins" style="left:490px;top:1822px"></div>
  <div class="avatar" role="img" aria-label="Portrait of Paul Reyes" style="left:632px;top:1822px"></div>
  <p class="quote right" style="top:1820px">Three generations of building know-how shows on every job site. Organised crews, honest communication and work done right the first time.<span class="who">Paul Reyes , Operations Manager</span></p>
</section>

<section class="likebar">
  <div class="rule" style="left:60px;width:316px"></div>
  <div class="rule" style="left:823px;width:316px"></div>
  <div class="like-pill">
    <svg class="abs" style="left:18px;top:14px" width="18" height="18" viewBox="0 0 24 24"><path d="M2 10h4v11H2zM8 21V10l5-8c1.5 0 2.5 1 2 3l-1 4h6a2 2 0 0 1 2 2l-2 8a2 2 0 0 1-2 2z" fill="none" stroke="#bbb" stroke-width="1.6"/></svg>
    <div class="abs" style="left:54px;top:0;height:44px;border-left:1px solid #e3e7ea"></div>
    <div class="like-badge"></div>
    <div class="like-text">You and 4.1k others like this.</div>
  </div>
</section>

<footer class="footer">
  <h4 style="left:52px">Contact Us</h4>
  <div class="col" style="left:52px;top:98px;width:260px">
    <p>Please feel free to contact us for any issue. Our staff is available to you from 9AM until 5PM on weekdays.</p>
    <p style="margin-top:14px"><b>Phone:</b> +1 (800) 555 01 87</p>
    <p style="margin-top:14px"><b>Office:</b> 412 Alder Lane, Denville</p>
    <p style="margin-top:14px"><b>Email:</b> info@pinecrestholdingsgroup.example</p>
  </div>
  <div class="f-social"><span></span><span></span><span></span><span></span><span></span></div>

  <h4 style="left:333px;width:534px;text-align:center">Headquarters</h4>
  <div class="map" role="img" aria-label="Street map showing the headquarters location">
    <svg class="abs" style="left:160px;top:92px" width="22" height="30" viewBox="0 0 24 32"><path d="M12 0a12 12 0 0 0-12 12c0 9 12 20 12 20s12-11 12-20A12 12 0 0 0 12 0z" fill="#d93a2f"/><circle cx="12" cy="12" r="4" fill="#7a1a14"/></svg>
  </div>

  <h4 style="left:895px">About Team</h4>
  <div class="col" style="left:895px;top:98px;width:255px">
    <p>Our team brings together builders, realtors, attorneys and property managers who know Northern New Jersey. We buy, renovate and sell homes that add value to every street we work on.</p>
    <p style="margin-top:14px">Whether you want to invest in a project or sell your house quickly and fairly, we keep the process clear, honest and simple from the first call to closing.</p>
  </div>

  <div class="f-rule"></div>
  <p class="copy">Copyright 2020 - Pinecrest Holdings Group. All rights reserved.</p>
</footer>

</body>
</html>
```